Create American style design suitable for consumers in Europe and America

We need a professional universal neutral design, which can be applied to all personal care tools, regardless of male and female, and the color matching needs to be matched by designers themselves.
Updates

设计质量低

Target Market(s)

Europe and America

Industry/Entity Type

personal care tools

Font styles to use
Serif
Sans Serif
Script

Requirements
Must have
• personal beauty care tool,like nail clipper,tweezer,scissors
Nice to have
• The copywriter plans on the packaging design can be applied to all personal care tools
Should not have
• Not designed for a single product, but for a whole personal care tool

```html
<!DOCTYPE html>
<html lang="en">
<head>
<meta charset="utf-8">
<title>Nolva Care – Nail Clipper Hang Card</title>
<link rel="stylesheet" href="https://fonts.googleapis.com/css2?family=Red+Hat+Display:wght@400;500;700&family=Oswald:wght@500&display=swap">
<style>
  :root {
    --stage: #231f20;
    --card-top: #ffffff;
    --card-shade: #f1f1f1;
    --gold: #fdc86a;
    --ink: #231f20;
    --hole: #231f20;
  }
  * { box-sizing: border-box; margin: 0; padding: 0; }
  html, body { width: 1200px; height: 1000px; overflow: hidden; }
  body {
    background: var(--stage);
    font-family: "Red Hat Display", Arial, sans-serif;
    color: var(--ink);
    position: relative;
  }
  .card {
    position: absolute;
    top: 76px;
    width: 507px;
    height: 848px;
    border-radius: 22px;
    overflow: hidden;
    background: radial-gradient(circle at 40% 35%, var(--card-top) 0%, var(--card-shade) 70%, var(--card-top) 100%);
  }
  .card--front { left: 74px; }
  .card--back { left: 617px; }
  .card__pattern { position: absolute; inset: 0; }
  .card__band {
    position: absolute; left: 0; right: 0; bottom: 0;
    height: 11px; background: var(--gold);
  }
  .hang-hole { position: absolute; left: 195px; top: 28px; }
  .brand {
    position: absolute; left: 0; right: 0; top: 106px;
    text-align: center;
    font-size: 42px; font-weight: 500; letter-spacing: 0.5px;
    color: var(--ink);
  }
  .product-name {
    position: absolute; left: 0; right: 0;
    text-align: center;
    font-size: 59px; font-weight: 700; line-height: 1;
    color: var(--gold); letter-spacing: 0.5px;
  }
  .product-tagline {
    position: absolute; left: 0; right: 0;
    text-align: center;
    font-size: 28.5px; font-weight: 400; line-height: 36px;
  }
  .card--front .product-name { top: 716px; }
  .card--front .product-tagline { top: 772px; }
  .card--back .product-name { top: 208px; }
  .card--back .product-tagline { top: 276px; }
  .description {
    position: absolute; left: 52px; width: 402px; top: 331px;
    font-size: 15.2px; line-height: 21.8px;
    text-align: justify; text-align-last: center;
    hyphens: auto;
  }
  .badge {
    position: absolute; top: 584px;
    width: 94px; height: 94px; border-radius: 50%;
    border: 1.5px solid var(--ink);
    display: flex; align-items: center; justify-content: center;
    text-align: center;
    font-family: "Oswald", "Arial Narrow", sans-serif;
    font-weight: 500; font-size: 15px; line-height: 18px;
  }
  .badge--steel { left: 136px; }
  .badge--satisfaction { left: 269px; }
  .contact {
    position: absolute; left: 0; right: 0; top: 706px;
    text-align: center; font-size: 18.5px; line-height: 25px;
  }
  .contact__heading {
    color: var(--gold); font-size: 17.5px; margin-bottom: 1px;
  }
</style>
</head>
<body>

  <section class="card card--front">
    <div class="card__pattern" role="img" aria-label="Soft background of overlapping grey and gold-outlined circles"></div>
    <svg class="hang-hole" width="117" height="40" viewBox="0 0 117 40">
      <rect x="0" y="14" width="117" height="26" rx="13" fill="var(--hole)"/>
      <circle cx="58.5" cy="14" r="11" fill="var(--hole)"/>
    </svg>
    <div class="brand">Nolva Care</div>
    <h1 class="product-name">NAIL CLIPPER</h1>
    <p class="product-tagline">Personal beauty care tool</p>
    <div class="card__band"></div>
  </section>

  <section class="card card--back">
    <div class="card__pattern" role="img" aria-label="Soft background of overlapping grey and gold-outlined circles"></div>
    <svg class="hang-hole" width="117" height="40" viewBox="0 0 117 40">
      <rect x="0" y="14" width="117" height="26" rx="13" fill="var(--hole)"/>
      <circle cx="58.5" cy="14" r="11" fill="var(--hole)"/>
    </svg>
    <div class="brand">Nolva Care</div>
    <h2 class="product-name">NAIL CLIPPER</h2>
    <p class="product-tagline">Personal beauty care tool</p>
    <p class="description">Lorem Ipsum is simply dummy text of the printing and typesetting industry. Lorem Ipsum has been the industry's standard dummy text ever since the 1500s, when an unknown printer took a galley of type and scrambled it to make a type specimen book. It has survived not only five centuries, but also the leap into electronic typesetting, remaining essentially unchanged. It was popularised in the 1960s with the release of Lettrix sheets containing Lorem Ipsum passages, and more recently with desktop publishing software like Pagecraft Studio including versions of Lorem Ipsum.</p>
    <div class="badge badge--steel">High<br>Quality<br>Stainless<br>Steel</div>
    <div class="badge badge--satisfaction">100%<br>Satisfaction<br>Guaranteed</div>
    <div class="contact">
      <p class="contact__heading">ANY QUESTIONS? CONTACT US</p>
      <p>PH: (555) 014-7890</p>
      <p>E: hello@nolvacare.com</p>
      <p>W: www.nolvacare.com</p>
    </div>
    <div class="card__band"></div>
  </section>

</body>
</html>
```